Packaging Design job - Product : Supplement for Travel Sickness

We need a packaging design for a travel sickness supplement called "VORELIX"

VORELIX It is a dietary supplement based on ginger which has properties fighting against motion sickness.

Ginger is a root used for many years for its beneficial effects on health. In addition to its stimulating and toning properties which help to resist fatigue, ginger is used as an adjuvant in case of nausea, vomiting and motion sickness. Ideal for pregnant women to combat certain disadvantages of pregnancy.

This product will be in blister form of 30 capsules. We need for this a packaging design for the box.Dimensions: 100 * 20 * 200 mm

We would like to see clean, modern and fresh designs.This should give the impression of professional products of pharmaceutical quality. You will also find attached the logo of our company.Ps : You can change the color of the logo

Mention to put on the box :

• Produit en France: Laboratoire KALDUNE, 24 Rue des Glaïeuls 37390 VERNOUX
• Distribué au Maroc: SORALUMIN 17 rue Ibn Zaydoun 30050 FEZ MAROC
• Complément alimentaire, ce n'est pas un médicament
• Voie orale
• Tenir hors de portée des enfants
• Respectez la dose recommandée
• Ce produit ne remplace pas une alimentation variée

Mode d'utilisation (How to use) :

2 à 3 gélules 30 min avant de prendre le véhicule de transport
1 gélule par jour en cas de cure

Font styles to use
Serif
Sans Serif
Script

Requirements
Should not have
• Sales and other "must buy" "guaranteed" etc

```html
<!DOCTYPE html>
<html lang="fr">
<head>
<meta charset="utf-8">
<title>VORELIX – Boîte 30 capsules</title>
<link rel="stylesheet" href="https://fonts.googleapis.com/css2?family=Josefin+Sans:wght@200;300&family=Lato:ital,wght@0,400;1,400&display=swap">
<style>
  :root {
    --stage: #f1f1ef;
    --board: #ffffff;
    --board-soft: #f6f6f5;
    --olive: #6b7158;
    --peach: #f0c694;
    --ink: #2c2c2c;
    --ink-soft: #4a4a4a;
    --line: #e6ded2;
  }
  * { margin: 0; padding: 0; box-sizing: border-box; }
  html, body { width: 1200px; height: 800px; overflow: hidden; background: var(--stage); }
  .canvas { position: relative; width: 1200px; height: 800px; }

  .panel { position: absolute; left: 120px; width: 960px; background: var(--board); overflow: hidden; box-shadow: 0 2px 10px rgba(0,0,0,.06); }
  .panel--front { top: 70px; height: 480px; }
  .panel--side { top: 580px; height: 110px; }

  .front-art { position: absolute; inset: 0; }

  .brand-title { position: absolute; left: 120px; top: 58px; font-family: "Josefin Sans", sans-serif; font-weight: 200; font-size: 132px; letter-spacing: 4px; color: var(--ink); line-height: 1; }
  .claim-band { position: absolute; left: 118px; top: 186px; width: 430px; height: 34px; background: var(--peach); display: flex; align-items: center; padding-left: 14px; }
  .claim-band span { font-family: "Lato", sans-serif; font-style: italic; font-size: 17px; color: var(--ink); }

  .route-tag { position: absolute; right: 48px; top: 66px; width: 190px; height: 190px; background: var(--olive); display: flex; flex-direction: column; justify-content: center; align-items: center; }
  .route-tag span { font-family: "Josefin Sans", sans-serif; font-weight: 300; font-size: 46px; line-height: 1; color: #fff; }
  .count { position: absolute; right: 60px; bottom: 34px; font-family: "Lato", sans-serif; font-size: 24px; color: #fff; letter-spacing: .5px; }

  .side-brand { position: absolute; left: 36px; top: 24px; font-family: "Josefin Sans", sans-serif; font-weight: 300; font-size: 58px; color: var(--ink); line-height: 1; }
  .side-claim { position: absolute; left: 330px; top: 32px; width: 150px; font-family: "Lato", sans-serif; font-size: 11px; line-height: 1.35; color: var(--ink-soft); }
  .side-copy { position: absolute; left: 500px; top: 24px; width: 400px; font-family: "Lato", sans-serif; font-size: 11px; line-height: 1.4; color: var(--ink); }
  .side-block { position: absolute; right: 0; bottom: 0; width: 120px; height: 12px; background: var(--olive); }
</style>
</head>
<body>
<main class="canvas">
  <section class="panel panel--front" aria-label="Face avant">
    <svg class="front-art" viewBox="0 0 960 480" width="960" height="480" aria-hidden="true">
      <ellipse cx="360" cy="160" rx="330" ry="150" fill="var(--board-soft)" stroke="var(--line)" stroke-width="1"/>
      <path d="M0 290 C 240 330, 560 360, 960 350 L 960 480 L 0 480 Z" fill="var(--peach)"/>
      <path d="M0 320 C 260 350, 560 388, 960 380 L 960 480 L 0 480 Z" fill="var(--board)"/>
      <path d="M0 372 C 300 420, 640 430, 960 400 L 960 480 L 0 480 Z" fill="var(--olive)"/>
    </svg>
    <h1 class="brand-title">VORELIX</h1>
    <div class="claim-band"><span>Complément alimentaire, ce n'est pas un médicament</span></div>
    <div class="route-tag"><span>voie</span><span>orale</span></div>
    <p class="count">30 Capsules</p>
  </section>

  <section class="panel panel--side" aria-label="Tranche">
    <h2 class="side-brand">VORELIX</h2>
    <p class="side-claim">Complément alimentaire, ce n'est pas un médicament</p>
    <p class="side-copy">Lorem ipsum dolor sit amet, consectetuer adipiscing elit, sed diam nonummy nibh euismod tincidunt ut laoreet dolore magna aliquam erat volutpat. Ut wisi enim ad minim veniam, quis nostrud exerci tation ullamcorper suscipit lobortis nisl ut aliquip ex ea commodo consequat. Duis autem vel eum iriure dolor in hendrerit in vulputate</p>
    <div class="side-block"></div>
  </section>
</main>
</body>
</html>
```